Bork Ventures, Inc. Website redesign

Revamp the website, it is old and outdated. www.borkventuresinc.example

Target Market(s)

Information Technology Consulting and Staffing

Coding

Coded - Design and coding required

Number of Pages Required

5+ page

Colors

Designer to choose colors to be used in the design.

Requirements
Must have
• Outlined text boxes just like from the Tolvane.example site. A clean look

```html
<!DOCTYPE html>
<html lang="en">
<head>
<meta charset="utf-8">
<title>Bork Ventures, Inc.</title>
<link href="https://fonts.googleapis.com/css2?family=Exo+2:wght@700;800&family=Montserrat:wght@400;500;600&family=Lato:ital,wght@0,400;0,700;1,700&display=swap" rel="stylesheet">
<style>
:root{
  --red:#9e1b32;
  --red-dark:#7e1426;
  --ink:#1e1e1e;
  --grey:#8c8c8c;
  --line:#dcdcdc;
  --soft:#f4f4f4;
  --night:#151515;
  --white:#ffffff;
}
*{margin:0;padding:0;box-sizing:border-box}
html,body{width:1200px;height:3906px;overflow:hidden;background:var(--white)}
body{position:relative;font-family:'Lato',sans-serif;color:var(--ink)}
.abs{position:absolute}
.heading{font-family:'Exo 2',sans-serif;font-weight:800;letter-spacing:1px;text-transform:uppercase;color:var(--ink)}
.brand{font-family:'Exo 2',sans-serif;font-weight:800;font-size:30px;letter-spacing:2px;color:var(--ink);display:flex;align-items:center;gap:12px}
.brand i{width:22px;height:22px;background:var(--red);display:block}

/* header */
.site-header{left:0;top:0;width:1200px;height:103px;background:var(--white)}
.main-nav a{position:absolute;top:43px;font-family:'Montserrat',sans-serif;font-size:14px;color:var(--grey);text-decoration:none;text-transform:uppercase;white-space:nowrap}
.main-nav a.active{color:var(--red);font-weight:600}
.nav-caret{left:469px;top:70px;width:0;height:0;border-left:6px solid transparent;border-right:6px solid transparent;border-bottom:10px solid var(--red)}

/* hero */
.hero{left:0;top:103px;width:1200px;height:625px;background:linear-gradient(180deg,#39404a 0%,#4b525c 45%,#5b6068 100%)}
.hero-title{left:0;top:290px;width:1200px;text-align:center;font-size:52px;color:var(--white)}
.hero-sub{left:300px;top:372px;width:600px;text-align:center;font-style:italic;font-weight:700;font-size:19px;line-height:32px;color:var(--white)}

/* strategy */
.strategy-card{left:77px;top:654px;width:1046px;height:469px;background:var(--white);box-shadow:0 2px 8px rgba(0,0,0,.12)}
.strategy-photo{left:664px;top:595px;width:459px;height:300px;background:var(--red)}
.strategy-photo div{position:absolute;left:10px;top:10px;width:439px;height:290px;background:linear-gradient(135deg,#2f3e5c,#6c7c98 60%,#3a4a6c)}
.strategy-title{left:120px;top:715px;font-size:39px}
.strategy-text{left:120px;top:780px;width:505px;font-size:16px;line-height:27px;color:var(--grey)}
.strategy-lead{left:120px;top:882px;font-family:'Montserrat',sans-serif;font-size:19px;color:#333}
.pillar{top:955px;width:180px;text-align:center}
.pillar svg{display:block;margin:0 auto 14px}
.pillar span{font-family:'Montserrat',sans-serif;font-size:19px;color:var(--ink)}

/* services */
.services-title{right:80px;top:1180px;font-size:40px}
.services-sub{right:80px;top:1246px;width:420px;text-align:right;font-size:16px;line-height:27px;color:var(--grey)}
.services-photo{left:77px;top:1344px;width:333px;height:489px;background:linear-gradient(160deg,#3a3b3c,#8a7e72 55%,#4a4a4c)}
.service{width:300px;text-align:right}
.service svg{display:block;margin-left:auto}
.service h3{font-family:'Montserrat',sans-serif;font-weight:400;font-size:19px;margin:18px 0 12px}
.service p{font-size:14px;line-height:26px;color:var(--grey)}

/* about */
.about{left:0;top:1896px;width:1200px;height:584px;background:radial-gradient(ellipse at 50% 50%,#2a2a2c 0%,var(--night) 70%)}
.about-title{left:0;top:1955px;width:1200px;text-align:center;font-size:40px;color:var(--white)}
.about-sub{left:0;top:2019px;width:1200px;text-align:center;font-family:'Montserrat',sans-serif;font-size:20px;color:var(--white)}
.about-copy{left:270px;top:2068px;width:660px;text-align:center;font-size:14px;line-height:26px;color:#e6e6e6}
.about-copy p+p{margin-top:27px}

/* news */
.news-title{left:0;top:2538px;width:1200px;text-align:center;font-size:40px}
.news-card{top:2615px;width:334px}
.news-photo{height:219px}
.news-date{position:absolute;left:0;top:28px;width:64px;text-align:center;color:var(--white)}
.news-date .day{background:#222;padding:5px 0 4px;font-family:'Montserrat',sans-serif}
.news-date .day b{display:block;font-size:20px;font-weight:500}
.news-date .day small{font-size:14px}
.news-date .yr{background:var(--red);font-size:13px;padding:5px 0}
.news-card p{font-family:'Montserrat',sans-serif;font-size:20px;line-height:29px;margin-top:22px;padding-left:2px}

/* contact */
.contact{left:0;top:3042px;width:1200px;height:626px;background:var(--soft)}
.contact-title{left:0;top:3100px;width:1200px;text-align:center;font-size:40px}
.callback{left:77px;top:3178px;width:681px;height:426px;background:var(--white);border-radius:8px;box-shadow:0 1px 6px rgba(0,0,0,.06)}
.callback-title{left:120px;top:3217px;font-family:'Montserrat',sans-serif;font-weight:600;font-size:30px}
.callback-sub{left:120px;top:3262px;font-family:'Montserrat',sans-serif;font-size:16px;color:var(--grey)}
.field{border:1px solid var(--line);border-radius:26px;display:flex;align-items:center;gap:12px;padding-left:22px;font-family:'Montserrat',sans-serif;font-size:14px;color:var(--grey)}
.field.area{border-radius:8px;align-items:flex-start;padding-top:16px}
.send-btn{left:120px;top:3513px;width:186px;height:50px;border-radius:25px;background:var(--red);color:var(--white);font-family:'Montserrat',sans-serif;font-size:17px;display:flex;align-items:center;justify-content:center}
.reach{left:791px;width:300px;text-align:center}
.reach .dot{width:58px;height:58px;border-radius:50%;background:var(--red);margin:0 auto 10px;display:flex;align-items:center;justify-content:center}
.reach span{display:block;font-size:15px;color:#555;line-height:25px}
.reach b{display:block;font-size:15px;color:#333;line-height:25px}

/* footer */
.site-footer{left:0;top:3668px;width:1200px;height:238px;background:#1a1a1a}
.site-footer .brand{color:var(--white)}
.footer-nav a{position:absolute;top:3734px;font-family:'Montserrat',sans-serif;font-size:16px;color:#e5e5e5;text-decoration:none;white-space:nowrap}
.footer-nav a.active{font-weight:600;color:var(--white)}
.footer-rule{left:77px;top:3809px;width:1046px;height:1px;background:#333}
.footer-mark{left:388px;top:3806px;width:44px;height:4px;background:var(--red)}
.social{top:3724px;width:47px;height:47px;border-radius:50%;display:flex;align-items:center;justify-content:center;font-family:'Montserrat',sans-serif;font-weight:600;font-size:14px}
.copyright{left:0;top:3850px;width:1200px;text-align:center;font-size:13px;color:#9a9a9a}
.copyright b{color:var(--white)}
</style>
</head>
<body>

<header class="abs site-header">
  <div class="abs brand" style="left:77px;top:34px"><i></i>BORK VENTURES</div>
  <nav class="main-nav">
    <a class="active" style="left:453px">Home</a>
    <a style="left:536px">About Us</a>
    <a style="left:651px">Services</a>
    <a style="left:755px">Strategy</a>
    <a style="left:869px">IT News</a>
    <a style="left:969px">Contact Us</a>
  </nav>
  <div class="abs nav-caret"></div>
  <svg class="abs" style="left:1100px;top:40px" width="24" height="24" viewBox="0 0 24 24" fill="none" stroke="#555" stroke-width="2"><circle cx="10" cy="10" r="7"/><path d="M15 15l6 6"/></svg>
</header>

<section class="abs hero" role="img" aria-label="Two consultants reviewing work on a laptop in an office"></section>
<h1 class="abs heading hero-title">Mission.Integrity.Results</h1>
<p class="abs hero-sub">Bork Ventures, Inc. is an 8(a) full-service IT consulting company based in the Washington, DC Metro area.</p>

<section class="abs strategy-card"></section>
<div class="abs strategy-photo"><div role="img" aria-label="Engineers working with a laptop inside a server room"></div></div>
<h2 class="abs heading strategy-title">Our Strategy</h2>
<p class="abs strategy-text">Civilian and Federal agencies are facing increased demands driven by the changing economic environment and shifts in the way products and services are sold and delivered.</p>
<p class="abs strategy-lead">These are the five pillars of our successful IT strategy</p>

<div class="abs pillar" style="left:83px">
  <svg width="56" height="56" viewBox="0 0 56 56" fill="none" stroke="var(--red)" stroke-width="2"><path d="M28 6a18 18 0 0 0-18 18c0 7 4 11 6 14v12h18v-6h6V34l4-4-4-6A18 18 0 0 0 28 6z"/><circle cx="27" cy="23" r="7"/><path d="M32 28l6 6"/></svg>
  <span>Assess</span>
</div>
<div class="abs pillar" style="left:295px">
  <svg width="56" height="56" viewBox="0 0 56 56" fill="none" stroke="var(--red)" stroke-width="2"><path d="M28 4l5 6 8-2 1 8 8 3-4 7 4 7-8 3-1 8-8-2-5 6-5-6-8 2-1-8-8-3 4-7-4-7 8-3 1-8 8 2z"/><path d="M20 27h5l5-8c2 0 3 1 3 3l-1 4h6c1 0 2 1 2 2l-2 8c0 1-1 2-2 2H25l-5-2z"/></svg>
  <span>Recommend</span>
</div>
<div class="abs pillar" style="left:509px">
  <svg width="56" height="56" viewBox="0 0 56 56" fill="none" stroke="var(--red)" stroke-width="2"><rect x="6" y="6" width="44" height="44"/><path d="M6 14h44"/><circle cx="28" cy="32" r="10"/><circle cx="28" cy="32" r="4"/></svg>
  <span>Implement</span>
</div>
<div class="abs pillar" style="left:722px">
  <svg width="56" height="56" viewBox="0 0 56 56" fill="none" stroke="var(--red)" stroke-width="2"><rect x="6" y="8" width="36" height="26"/><path d="M18 40h12M24 34v6"/><rect x="34" y="20" width="16" height="28"/><path d="M12 16h24M12 22h18M12 28h22"/></svg>
  <span>Monitor</span>
</div>
<div class="abs pillar" style="left:935px">
  <svg width="56" height="56" viewBox="0 0 56 56" fill="none" stroke="var(--red)" stroke-width="2"><circle cx="16" cy="10" r="5"/><path d="M8 50V22h16v28M12 50V34M20 50V34"/><circle cx="40" cy="30" r="8"/><circle cx="40" cy="30" r="3"/><circle cx="44" cy="12" r="5"/></svg>
  <span>Manage</span>
</div>

<h2 class="abs heading services-title">Our Services</h2>
<p class="abs services-sub">Our people and our process is what makes us successful in providing these services.</p>
<div class="abs services-photo" role="img" aria-label="Technician kneeling with a laptop and phone beside server racks"></div>

<div class="abs service" style="left:465px;top:1344px">
  <svg width="84" height="84" viewBox="0 0 84 84" fill="none" stroke="var(--red)" stroke-width="2.4"><rect x="30" y="4" width="50" height="40"/><circle cx="55" cy="22" r="9"/><circle cx="18" cy="56" r="12"/><path d="M4 80h30M12 68v12M24 68v12M40 56h34"/><circle cx="74" cy="72" r="6"/></svg>
  <h3>Hardware / Software Sales</h3>
  <p>We have access to multiple distributor partners throughout North America, as well as Elite Partner Status</p>
</div>
<div class="abs service" style="left:821px;top:1344px">
  <svg width="84" height="84" viewBox="0 0 84 84" fill="none" stroke="var(--red)" stroke-width="2.4"><path d="M42 4l6 8 10-3 2 10 10 4-4 9 6 8-8 6 1 10-10 1-4 9-9-5-9 5-4-9-10-1 1-10-8-6 6-8-4-9 10-4 2-10 10 3z"/><circle cx="42" cy="42" r="14"/><path d="M46 36c-2-2-8-2-8 2s8 2 8 6-6 4-8 2M42 32v20"/></svg>
  <h3>Professional Services</h3>
  <p>Our team provides experienced leadership and guidance, utilizing the industry standard methodologies.</p>
</div>
<div class="abs service" style="left:465px;top:1614px">
  <svg width="84" height="84" viewBox="0 0 84 84" fill="none" stroke="var(--red)" stroke-width="2.4"><rect x="8" y="4" width="40" height="76"/><circle cx="18" cy="18" r="4"/><circle cx="30" cy="18" r="4"/><path d="M14 34h28M14 44h28M14 54h20"/><circle cx="62" cy="46" r="8"/><path d="M48 80c0-12 6-18 14-18s14 6 14 18z"/></svg>
  <h3>Technology Assessment</h3>
  <p>Experience has shown companies that perform objective, third-party technology assessments.</p>
</div>
<div class="abs service" style="left:821px;top:1614px">
  <svg width="84" height="84" viewBox="0 0 84 84" fill="none" stroke="var(--red)" stroke-width="2.4"><rect x="4" y="14" width="64" height="46"/><path d="M28 72h16M36 60v12M12 28h20M12 36h14"/><circle cx="48" cy="34" r="6"/><circle cx="74" cy="12" r="7"/></svg>
  <h3>Technology Consulting</h3>
  <p>Implementing quality solutions is more than applying technology to problems. You need experts.</p>
</div>

<section class="abs about" role="img" aria-label="Dimly lit data center corridor"></section>
<h2 class="abs heading about-title">About Us</h2>
<p class="abs about-sub">Bringing Thought Leadership and Quality to Every Project</p>
<div class="abs about-copy">
  <p>Bork Ventures, Inc. is an 8(a) innovative and rapidly growing full-service IT consulting firm. We provide our clients with cutting-edge technologies and the know-how to apply them to their individual business models.</p>
  <p>For over 20 + years, we have been providing reliable IT solutions to businesses in the Washington, DC Metro area and beyond. Our comprehensive services provide clients with unique technology solutions that are customized to meet the specific demands of their business.</p>
  <p>Look to our experts for strategic IT guidance, management and services that allows you to take your mind off technology and concentrate on your core area of business. Bork Ventures, Inc. provides cost-efficient solutions that simply make good sense.</p>
</div>

<h2 class="abs heading news-title">Latest News</h2>
<article class="abs news-card" style="left:77px">
  <div class="news-photo" role="img" aria-label="Colleagues gathered around a laptop" style="background:linear-gradient(135deg,#d9b48a,#6d5a48)"></div>
  <div class="news-date"><div class="day"><b>04</b><small>Sep</small></div><div class="yr">2019</div></div>
  <p>Lorem ipsum dolor sit consectetur dolore magna aliqua.</p>
</article>
<article class="abs news-card" style="left:434px">
  <div class="news-photo" role="img" aria-label="Two coworkers discussing work at a laptop" style="background:linear-gradient(135deg,#e8ecef,#7e8a96)"></div>
  <div class="news-date"><div class="day"><b>05</b><small>Sep</small></div><div class="yr">2019</div></div>
  <p>Lorem ipsum dolor sit consectetur dolore magna aliqua.</p>
</article>
<article class="abs news-card" style="left:789px">
  <div class="news-photo" role="img" aria-label="Team meeting around a conference table" style="background:linear-gradient(135deg,#f2f2f0,#9aa0a4)"></div>
  <div class="news-date"><div class="day"><b>06</b><small>Sep</small></div><div class="yr">2019</div></div>
  <p>Lorem ipsum dolor sit consectetur dolore magna aliqua.</p>
</article>

<section class="abs contact"></section>
<h2 class="abs heading contact-title">Contact Us</h2>
<div class="abs callback"></div>
<h3 class="abs callback-title">Request Call Back</h3>
<p class="abs callback-sub">We are here to answer any question you may have</p>
<svg class="abs" style="left:648px;top:3218px" width="70" height="62" viewBox="0 0 70 62" fill="none" stroke="#bbb" stroke-width="1.5"><path d="M68 2L2 32l22 6zM68 2L24 38l6 20 10-14zM68 2L40 44l16 8z"/></svg>
<div class="abs field" style="left:120px;top:3310px;width:290px;height:49px"><svg width="14" height="14" viewBox="0 0 14 14" fill="#777"><circle cx="7" cy="4" r="3.5"/><path d="M0 14c0-5 3-6 7-6s7 1 7 6z"/></svg>Your Name :</div>
<div class="abs field" style="left:120px;top:3378px;width:290px;height:49px"><svg width="14" height="12" viewBox="0 0 14 12" fill="none" stroke="#777" stroke-width="1.5"><rect x="1" y="1" width="12" height="10"/><path d="M1 1l6 5 6-5"/></svg>Enter Email :</div>
<div class="abs field" style="left:120px;top:3445px;width:290px;height:50px"><svg width="14" height="14" viewBox="0 0 24 24" fill="#777"><path d="M6 2l4 5-2 3c1 3 3 5 6 6l3-2 5 4-3 4C10 22 2 14 2 5z"/></svg>Phone Number :</div>
<div class="abs field area" style="left:426px;top:3310px;width:292px;height:185px"><svg width="14" height="14" viewBox="0 0 14 14" fill="#777"><path d="M10 1l3 3-8 8H2V9z"/></svg>Message / Comments :</div>
<div class="abs send-btn">SEND MESSAGE</div>

<div class="abs reach" style="top:3175px">
  <div class="dot"><svg width="24" height="24" viewBox="0 0 24 24" fill="#fff"><path d="M6 2l4 5-2 3c1 3 3 5 6 6l3-2 5 4-3 4C10 22 2 14 2 5z"/></svg></div>
  <span>Call Us</span><b>301-555-0142</b>
</div>
<div class="abs reach" style="top:3320px">
  <div class="dot"><svg width="24" height="20" viewBox="0 0 24 20" fill="#fff"><path d="M1 2h22v16H1z"/><path d="M1 2l11 9 11-9" stroke="#9e1b32" stroke-width="2" fill="none"/></svg></div>
  <span>Mail us</span><b>info@borkventures.example</b>
</div>
<div class="abs reach" style="top:3462px">
  <div class="dot"><svg width="20" height="26" viewBox="0 0 20 26" fill="#fff"><path d="M10 0a10 10 0 0 0-10 10c0 7 10 16 10 16s10-9 10-16A10 10 0 0 0 10 0z"/><circle cx="10" cy="10" r="4" fill="#9e1b32"/></svg></div>
  <span>Our Location</span><b>4820 Alderbrook Ln Calverton,</b><b>MD 20705</b>
</div>

<footer class="abs site-footer"></footer>
<div class="abs brand" style="left:77px;top:3728px;color:#fff"><i></i>BORK VENTURES</div>
<nav class="footer-nav">
  <a class="active" style="left:388px">Home</a>
  <a style="left:464px">About Us</a>
  <a style="left:564px">Services</a>
  <a style="left:659px">Strategy</a>
  <a style="left:754px">It News</a>
  <a style="left:842px">Contact Us</a>
</nav>
<div class="abs footer-rule"></div>
<div class="abs footer-mark"></div>
<div class="abs social" style="left:1013px;background:var(--red);color:#fff">f</div>
<div class="abs social" style="left:1075px;background:#fff;color:#222">in</div>
<p class="abs copyright">Copyright © <b>Bork Ventures</b> - 2019 . All Right Reserved</p>

</body>
</html>
```